New boutique hotel for tourists, with hint of art deco styling

This is a new, soon to be completed, boutique hotel in Sydney. A letterhead with a logo is required. Less emphasis on the word "boutique". Perhaps the word could be screened to be lighter in colour (or print intensity). Would like a simple, clear, easy-to read, sans serif type face. The information on the letterhead is:
Mrs Tolliver Boutique Hotel
412 Quenby Street,
Larchmere, NSW, 2047
Australia
Tel: +61 2 9468-0000
mrstolliverhotel@quelmail.example
mrstolliverhotel.example.au
ABN 47 902 365 184

Target Market(s)

travellers, tourists, various ages

Industry/Entity Type

Hospitality

Contact Information for Business Card

Mrs Tolliver Boutique Hotel
412 Quenby Street,
Larchmere, NSW, 2047
Telephone: (02) 9468-0000
www.mrstolliverhotel.example.au
mrstolliverhotel@quelmail.example
ABN 47 902 365 184

Logo Text

suggest playing with the letter "T"

Font styles to use
Sans Serif

Colors
3176b5

Requirements
Must have
• ABN to be very small.
• Must be clear, easy to read and in a sans serif typeface, please!
Nice to have
• The word "Boutique" should be less intense in appearance to the rest of the name, or even "Boutique Hotel" can have less prominence than "Mrs Tolliver".
Should not have
• No serif typeface. Sans serif only will be accepted.

```html
<!DOCTYPE html>
<html lang="en">
<head>
<meta charset="utf-8">
<title>Mrs Tolliver Boutique Hotel – Letterhead</title>
<link rel="stylesheet" href="https://fonts.googleapis.com/css2?family=Arimo:wght@700&family=Questrial&display=swap">
<style>
  :root {
    --brand-blue: #3176b5;
    --paper: #ffffff;
    --on-brand: #ffffff;
    --backdrop: #e9ecef;
  }
  * { box-sizing: border-box; margin: 0; padding: 0; }
  html, body {
    width: 100%;
    height: 100%;
    overflow: hidden;
    background: var(--backdrop);
  }
  .letterhead {
    position: relative;
    width: 848px;
    height: 1200px;
    margin: 0 auto;
    background: var(--paper);
    overflow: hidden;
  }
  .brand {
    position: absolute;
    left: 31px;
    top: 46px;
    display: flex;
    flex-direction: column;
    align-items: center;
    color: var(--brand-blue);
  }
  .brand-dot {
    display: block;
    width: 64px;
    height: 64px;
    border-radius: 50%;
    background: var(--brand-blue);
    margin-bottom: 14px;
  }
  .brand-name {
    font-family: "Arimo", Arial, sans-serif;
    font-weight: 700;
    font-size: 46px;
    line-height: 1;
    letter-spacing: -1.5px;
  }
  .brand-sub {
    margin-top: 10px;
    font-family: "Questrial", Arial, sans-serif;
    font-weight: 400;
    font-size: 17px;
    line-height: 1;
    letter-spacing: 1.6px;
    text-transform: uppercase;
  }
  .footer-band {
    position: absolute;
    left: 0;
    bottom: 0;
    width: 100%;
    height: 203px;
    background: var(--brand-blue);
    color: var(--on-brand);
  }
  .footer-name {
    position: absolute;
    left: 31px;
    top: 24px;
    font-family: "Arimo", Arial, sans-serif;
    font-weight: 700;
    font-size: 31px;
    letter-spacing: -1px;
    line-height: 1;
  }
  .contact-list,
  .address {
    position: absolute;
    top: 76px;
    font-family: "Questrial", Arial, sans-serif;
    font-size: 22px;
    line-height: 30px;
    font-style: normal;
    list-style: none;
    white-space: nowrap;
  }
  .contact-list { left: 31px; }
  .address { left: 400px; top: 80px; }
  .abn {
    position: absolute;
    left: 664px;
    top: 148px;
    font-family: "Questrial", Arial, sans-serif;
    font-size: 14px;
    letter-spacing: -0.3px;
    white-space: nowrap;
  }
</style>
</head>
<body>
  <main class="letterhead">
    <header class="brand" aria-label="Mrs Tolliver Boutique Hotel">
      <span class="brand-dot" aria-hidden="true"></span>
      <span class="brand-name">Mrs Tolliver</span>
      <span class="brand-sub">Boutique Hotel</span>
    </header>

    <footer class="footer-band">
      <p class="footer-name">Mrs. Tolliver</p>
      <ul class="contact-list">
        <li>mrstolliverhotel@quelmail.example</li>
        <li>mrstolliverhotel.example.au</li>
        <li>Tel: +61 2 9468-0000</li>
      </ul>
      <address class="address">
        412 Quenby Street<br>
        Larchmere, NSW, 2047<br>
        Australia
      </address>
      <p class="abn">ABN 47 902 365 184</p>
    </footer>
  </main>
</body>
</html>
```